Award-winnning Estate Agent needs a premium version of their 'For Sale' board design

We need a premium option for our 'For Sale' board design. We have a standard board that is attached to this brief, but were are looking to have a premium design version that we will use when selling exclusive properties. Our company name is Harbourline Vale Estates and the name for this is exclusive selection is: 'The Harbourline Collection'. The design needs to work with our current brand, but have a distinctive PREMIUM feel to it. I have uploaded the barnd guidelines and also some of the exisisting logo variations. We do NOT need a new logo but feel free to play around with colours, fonts, sizes etc. for the sign.

Target Market(s)

Property buyers & house hunters

Industry/Entity Type

Real Estate - Residential Property

Font styles to use
Sans Serif

Requirements
Must have
• A premium fee, must be square design, must be easy to read when driving past the sign
Nice to have
• I'm open ot ideas

```html
<!DOCTYPE html>
<html lang="en">
<head>
<meta charset="utf-8">
<title>The Harbourline Collection – For Sale Board</title>
<link rel="stylesheet" href="https://fonts.googleapis.com/css2?family=Montserrat:wght@400;600;800&family=Roboto+Condensed:wght@700&display=swap">
<style>
  :root {
    --navy: #2e3484;
    --brand-blue: #1175bd;
    --premium-gold: #d4b46a;
    --post-grey: #d9d9d9;
    --chain: #3a3a3a;
    --white: #ffffff;
    --page: #ffffff;
  }
  html, body {
    margin: 0;
    padding: 0;
    width: 1200px;
    height: 960px;
    overflow: hidden;
    background: var(--page);
  }
  .board-scene { display: block; width: 1200px; height: 960px; }
  .post { fill: var(--post-grey); }
  .chain { fill: none; stroke: var(--chain); stroke-width: 4; }
  .board-frame { fill: var(--navy); }
  .board-panel { fill: var(--brand-blue); }
  .premium-keyline { fill: none; stroke: var(--premium-gold); stroke-width: 2; }
  .collection-name {
    fill: var(--premium-gold);
    font-family: "Montserrat", sans-serif;
    font-weight: 600;
    font-size: 15px;
    letter-spacing: 5px;
  }
  .headline {
    fill: var(--white);
    font-family: "Montserrat", sans-serif;
    font-weight: 800;
    font-size: 192px;
  }
  .brand-mark { fill: var(--white); }
  .brand-name {
    fill: var(--white);
    font-family: "Montserrat", sans-serif;
    font-weight: 600;
    font-size: 21px;
  }
  .phone {
    fill: var(--white);
    font-family: "Montserrat", sans-serif;
    font-weight: 800;
    font-size: 74px;
  }
  .web-address {
    fill: var(--white);
    font-family: "Roboto Condensed", sans-serif;
    font-weight: 700;
    font-size: 40px;
  }
  .rule { fill: var(--premium-gold); }
</style>
</head>
<body>
<svg class="board-scene" viewBox="0 0 1200 960" xmlns="http://www.w3.org/2000/svg">
  <g class="post-frame">
    <polygon class="post" points="902,112 946,0 990,112 990,960 902,960"/>
    <path class="post" d="M194,160 H1112 Q1124,160 1116,170 L1048,256 Q1042,264 1032,264 H272 Q262,264 256,256 L188,170 Q182,160 194,160 Z"/>
  </g>

  <g class="chains">
    <ellipse class="chain" cx="360" cy="276" rx="6" ry="10"/>
    <ellipse class="chain" cx="360" cy="300" rx="6" ry="10"/>
    <ellipse class="chain" cx="796" cy="276" rx="6" ry="10"/>
    <ellipse class="chain" cx="796" cy="300" rx="6" ry="10"/>
  </g>

  <g class="board">
    <rect class="board-frame" x="275" y="314" width="610" height="608"/>
    <rect class="board-panel" x="308" y="346" width="545" height="478"/>
    <rect class="premium-keyline" x="315" y="353" width="531" height="464"/>

    <text class="collection-name" x="580" y="336" text-anchor="middle">THE HARBOURLINE COLLECTION</text>

    <text class="headline" x="581" y="509" text-anchor="middle" textLength="400" lengthAdjust="spacingAndGlyphs">FOR</text>
    <text class="headline" x="581" y="664" text-anchor="middle" textLength="496" lengthAdjust="spacingAndGlyphs">SALE</text>

    <g class="brand-line">
      <rect class="brand-mark" x="440" y="710" width="24" height="24"/>
      <text class="brand-name" x="474" y="730" textLength="262" lengthAdjust="spacingAndGlyphs">Harbourline Vale Estates</text>
    </g>

    <text class="phone" x="581" y="812" text-anchor="middle" textLength="510" lengthAdjust="spacingAndGlyphs">01632 960412</text>

    <text class="web-address" x="580" y="870" text-anchor="middle" textLength="510" lengthAdjust="spacingAndGlyphs">www.harbourlinevaleestates.co.uk</text>
    <rect class="rule" x="308" y="886" width="545" height="3"/>
  </g>
</svg>
</body>
</html>
```